Residential Mortgage Leader needs Wordpress Design

Looking for a home page website design for a client. We develop using the WordPress platform and would prefer the design be at least loosely based on an existing WordPress template. Attached files have many notes from our creative brief with client. The site must be responsive. Approved, basic wireframe attached. There is room for interpretation.

Existing web site: http://www.marisolkettering.example/

The Marisol Kettering Team relies on strong systems to deliver an on-time, done-right, friendly experience. Marisol offers mortgages and refinancing services throughout the United States. She is a successful Brookvale Funding agent who strives to be an active part of her community. She would like to focus the site on her team, rather than just her.

Difference makers...
When you work with the Marisol Kettering team you get a high level of expertise and a friendly experience.

She has amazing credentials. Marisol is widely recognized as a top producer for her company, and has earned a number of awards and honors for her customer service.

Marisol's team is very engaged and enjoys sharing social comments or photos from their community.

Imagery:
* Friendly, warm imagery, preferably of her team or an image to represent her team
* Clean and crisp
* Professional / Experts in mortgage and refinance
* Clean / Good use of white space
Updates

When possible, please use imagery from the DFW area. The client mentioned they would prefer not to see stock images. Thanks.

Amend that- creative use of stock images, however, is fine. A few designs have used stock imagery, but in a well-considered manner.

We added some photos and graphics that are local. We are Dallas / Ft. Worth, Plano, Frisco, Texas. We also added some examples of photos to use for the "In the Community" area. Stock photos of business folks just doesn't fit there. Thanks!

Target Market(s)

They service a lot of builders, but also work with homeowners. Their typical client is usually a woman searching for mortgage services online. She typically has a family and may refer her husband to Marisol's team. Keep in mind, however, they also see a number of other scenarios. Most of their clients are middle to high-end borrowers.

Industry/Entity Type

It Company

Requirements
Must have
• Design should be developed using program such as Photoshop or Fireworks or Illustrator as last preference. Ideally, the design would be based on an existing responsive WordPress theme, which we would customize. You must include the name of the target theme. The footer should include lots of space for disclaimers and legal language. Site navigation should include these choices: "Home, About, Builders, Mortgage Info, Approval, Blog, Contact"
Nice to have
• Blog, social media and photos area. Use of the already approved style prototype with colors and fonts (Lato- a Google font, Times New Roman and Cookie-a decorative Google font). However, we are open to interpretation.
Should not have
• Hard to read fonts or a lack of white space.

```html
<!DOCTYPE html>
<html lang="en">
<head>
<meta charset="utf-8">
<title>Brookvale Funding – Marisol Kettering Team</title>
<link href="https://fonts.googleapis.com/css2?family=Lato:wght@400;700&family=Cookie&family=Tinos&display=swap" rel="stylesheet">
<style>
  :root{
    --blue:#0f86bb;
    --blue-dark:#0b6f9c;
    --nav-top:#2d2d2d;
    --nav-bottom:#121212;
    --red:#c33a25;
    --page:#ededed;
    --card:#f7f7f7;
    --rule:#cfcfcf;
    --text:#555;
    --muted:#8a8a8a;
    --footer:#333333;
    --footer-bar:#2a2a2a;
    --footer-text:#c9c9c9;
    --white:#fff;
  }
  *{box-sizing:border-box;margin:0;padding:0}
  html,body{width:850px;height:1200px;overflow:hidden}
  body{font-family:'Lato',sans-serif;background:var(--page);color:var(--text)}
  .page{position:relative;width:850px;height:1200px;overflow:hidden;background:var(--page)}
  .abs{position:absolute}

  /* header */
  .site-header{position:absolute;left:0;top:0;width:850px;height:88px;background:var(--blue);border-top:5px solid #1a1a1a}
  .brand{position:absolute;left:78px;top:30px;color:var(--white)}
  .brand-name{font-weight:700;font-size:22px;letter-spacing:-.2px;line-height:1}
  .brand-sub{font-weight:700;font-size:10px;margin-top:4px}
  .contact-cta{position:absolute;left:640px;top:28px;display:flex;align-items:center;gap:8px;color:var(--white)}
  .contact-cta .label{font-size:11px;line-height:1.2}
  .contact-cta .phone{font-size:13px;line-height:1.2}

  /* nav */
  .main-nav{position:absolute;left:0;top:88px;width:850px;height:36px;background:linear-gradient(var(--nav-top),var(--nav-bottom))}
  .main-nav a{position:absolute;top:0;height:36px;line-height:36px;color:var(--white);font-size:11px;text-decoration:none}
  .main-nav a.active{background:var(--red);padding:0 10px}
  .search{position:absolute;left:636px;top:7px;width:138px;height:22px;border:1px solid #555;background:#1c1c1c;color:#9a9a9a;font-size:8px;padding:0 6px;line-height:20px}

  /* hero */
  .hero{position:absolute;left:0;top:124px;width:850px;height:276px;background:var(--blue)}
  .hero-photo{position:absolute;left:78px;top:0}
  .hero-copy{position:absolute;left:515px;top:16px;width:260px;color:var(--white)}
  .hero-title{font-family:'Cookie',cursive;font-size:36px;font-weight:400;line-height:1}
  .hero-text{font-size:9px;line-height:12.8px;margin-top:12px}
  .hero-link{display:inline-block;margin-top:12px;font-family:'Tinos',serif;font-size:11px;color:var(--white)}

  /* intro */
  .intro{position:absolute;left:80px;top:416px;width:690px;text-align:center;font-family:'Tinos',serif;font-size:17.5px;line-height:24px;color:var(--text)}

  /* feature columns */
  .feature{position:absolute;top:482px}
  .feature h2{font-family:'Tinos',serif;font-weight:400;font-size:19px;color:var(--blue);padding-left:8px;height:28px;border-bottom:2px solid var(--rule)}
  .feature .body{background:var(--card);height:110px;padding:12px 8px 0;font-size:8.6px;line-height:12.8px;color:var(--muted)}
  .feature p + p{margin-top:13px}

  /* community band */
  .community-title{position:absolute;left:0;top:646px;width:850px;text-align:center;font-family:'Cookie',cursive;font-size:40px;color:var(--blue);line-height:1}
  .community-sub{position:absolute;left:0;top:696px;width:850px;text-align:center;font-family:'Tinos',serif;font-size:16px;color:var(--text)}
  .band-rule{position:absolute;left:0;top:727px;width:850px;height:2px;background:var(--rule)}

  .block-title{position:absolute;top:758px;font-family:'Tinos',serif;font-size:16px;color:var(--blue);font-weight:400}
  .blog-post{position:absolute;left:77px;width:190px}
  .blog-post h3{font-weight:400;font-size:12px;color:#444}
  .blog-post p{font-size:8.6px;line-height:12.8px;color:var(--muted);margin-top:3px}

  .social-row{position:absolute;left:333px;display:flex;gap:12px}
  .social-icon{width:38px;height:36px;background:var(--white);display:flex;align-items:center;justify-content:center}
  .social-row h3{font-weight:400;font-size:12.5px;color:#444;margin-top:1px}
  .social-row p{font-size:8.6px;color:var(--muted);margin-top:5px}

  .gallery{position:absolute;left:575px;top:790px;display:grid;grid-template-columns:repeat(3,61px);grid-auto-rows:56px;column-gap:7px;row-gap:8px}
  .gallery span{display:block;border:2px solid var(--white)}

  /* footer */
  .site-footer{position:absolute;left:0;top:942px;width:850px;height:210px;background:var(--footer);color:var(--footer-text)}
  .agent-photo{position:absolute;left:77px;top:30px;width:102px;height:118px;background:linear-gradient(160deg,#8a8d92,#5b5550 60%,#2d2a28);border:1px solid #555}
  .agent{position:absolute;left:186px;top:30px}
  .agent h3{font-weight:400;font-size:13px;color:var(--white);line-height:15px}
  .agent ul{list-style:none;margin-top:6px;font-size:9.6px;line-height:16.4px}
  .agent .directions{position:absolute;top:154px;left:0;font-size:9.6px;color:var(--white)}
  .foot-col{position:absolute;top:30px}
  .foot-col h4{font-weight:400;font-size:13px;color:var(--white)}
  .foot-col ul{list-style:none;margin-top:10px;font-size:9.6px;line-height:16.4px}
  .lang{margin-top:14px;width:77px;height:23px;background:#272727;font-size:9.6px;line-height:23px;padding-left:8px;position:relative}
  .lang svg{position:absolute;right:8px;top:8px}
  .footer-bar{position:absolute;left:0;top:1152px;width:850px;height:48px;background:var(--footer-bar)}
  .copyright{position:absolute;left:88px;top:17px;font-size:9.6px;color:var(--footer-text)}
  .footer-badges{position:absolute;left:656px;top:12px;display:flex;gap:4px;align-items:center}
  .footer-badges span{width:23px;height:23px;border-radius:3px}
</style>
</head>
<body>
<div class="page">

  <header class="site-header">
    <div class="brand">
      <div class="brand-name">Brookvale Funding</div>
      <div class="brand-sub">A Hollins Ridge Company</div>
    </div>
    <div class="contact-cta">
      <svg width="26" height="30" viewBox="0 0 26 30" aria-hidden="true">
        <path d="M4 15 V12 a9 9 0 0 1 18 0 V15" fill="none" stroke="#1a1a1a" stroke-width="2.4"/>
        <rect x="2" y="13" width="6" height="10" rx="2" fill="#1a1a1a"/>
        <rect x="18" y="13" width="6" height="10" rx="2" fill="#1a1a1a"/>
        <path d="M21 23 q0 5 -7 5" fill="none" stroke="#1a1a1a" stroke-width="1.6"/>
        <circle cx="13" cy="28" r="1.8" fill="#1a1a1a"/>
      </svg>
      <div>
        <div class="label">Work With Us:</div>
        <div class="phone">0800-5550-142-7</div>
      </div>
    </div>
  </header>

  <nav class="main-nav">
    <a class="active" href="#" style="left:78px">Home</a>
    <a href="#" style="left:149px">About Us</a>
    <a href="#" style="left:222px">Builders</a>
    <a href="#" style="left:289px">Mortgage Info</a>
    <a href="#" style="left:386px">Blog</a>
    <a href="#" style="left:434px">Contact Us</a>
    <div class="search">Enter your search...</div>
  </nav>

  <section class="hero">
    <svg class="hero-photo" width="542" height="276" viewBox="0 0 542 276" role="img" aria-label="Smiling couple in front of a brick family home with a green lawn">
      <defs>
        <linearGradient id="heroFill" x1="0" y1="0" x2="0" y2="1">
          <stop offset="0" stop-color="#b9c8d4"/>
          <stop offset=".45" stop-color="#a39684"/>
          <stop offset=".7" stop-color="#5f8a3a"/>
          <stop offset="1" stop-color="#3f6e22"/>
        </linearGradient>
      </defs>
      <polygon points="0,0 266,0 542,276 0,276" fill="url(#heroFill)"/>
    </svg>
    <div class="hero-copy">
      <h1 class="hero-title">Earning Your Business</h1>
      <p class="hero-text">Lorem ipsum dolor sit amet, consectetur adipisicing elit, sed do eiusmod tempor incididunt ut labore et dolore magna aliqua. Ut enim ad minim veniam, quis nostrud exercitation ullamco laboris nisi ut aliquip ex ea commodo consequat. Duis aute irure dolorpariatur....</p>
      <a class="hero-link" href="#">Get to Know Us</a>
    </div>
  </section>

  <p class="intro">Lorem ipsum dolor sit amet, consectetur adipisicing elit, sed do eiusmod tempor incididunt ut labore et dolore magna aliqua.</p>

  <article class="feature" style="left:85px;width:261px">
    <h2>Our Credentials</h2>
    <div class="body">
      <p>Lorem ipsum dolor sit amet, consectetur adipisicing exercitation ullamco elit, sed do eiusmod tempor veniam, quis nostrud exercitation ullamco incididunt ut labore et dolore magna aliqua.</p>
      <p>Ut enim ad minim veniam, quis nostrud exercitation ullamco laboris nisi ut aliquip ex ea commodo consequat.</p>
    </div>
  </article>
  <article class="feature" style="left:358px;width:198px">
    <h2>Awards</h2>
    <div class="body">
      <p>Lorem ipsum dolor sit amet, consectetur adipisicing elit, sed do eiusmod tempor incididunt ut labore et dolore magna aliqua.</p>
      <p>Ut enim ad minim veniam, quis nostrud exercitation ullamco laboris nisi ut aliquip....</p>
    </div>
  </article>
  <article class="feature" style="left:568px;width:198px">
    <h2>Recognion</h2>
    <div class="body">
      <p>Lorem ipsum dolor sit amet, consectetur adipisicing elit, sed do eiusmod tempor incididunt ut labore et dolore magna aliqua.</p>
      <p>Ut enim ad minim veniam, quis nostrud exercitation ullamco laboris nisi ut aliquip....</p>
    </div>
  </article>

  <h2 class="community-title">Engaged In Our Community</h2>
  <p class="community-sub">Connect With Us</p>
  <div class="band-rule"></div>

  <h2 class="block-title" style="left:77px">Blog</h2>
  <div class="blog-post" style="top:788px">
    <h3>• Borrowing</h3>
    <p>Sed ut perspiciatis unde omnis iste natus error sit voluptatem accusantium doloremque laudantium...</p>
  </div>
  <div class="blog-post" style="top:853px">
    <h3>• Best Practices</h3>
    <p>Sed ut perspiciatis unde omnis iste natus error sit voluptatem accusantium doloremque laudantium...</p>
  </div>

  <h2 class="block-title" style="left:333px">Social Icons</h2>
  <div class="social-row" style="top:789px">
    <div class="social-icon"><svg width="14" height="14" aria-hidden="true"><rect x="1" y="1" width="12" height="12" fill="#555"/></svg></div>
    <div><h3>Neighbor Feed</h3><p>Lorem ipsum dolor sit amet...</p></div>
  </div>
  <div class="social-row" style="top:832px">
    <div class="social-icon"><svg width="14" height="14" aria-hidden="true"><circle cx="7" cy="7" r="6" fill="#555"/></svg></div>
    <div><h3>Chirp</h3><p>Lorem ipsum dolor sit amet...</p></div>
  </div>
  <div class="social-row" style="top:874px">
    <div class="social-icon">
      <svg width="18" height="18" viewBox="0 0 18 18" aria-hidden="true">
        <circle cx="3" cy="15" r="2" fill="#555"/>
        <path d="M1 8 a9 9 0 0 1 9 9" fill="none" stroke="#555" stroke-width="2.2"/>
        <path d="M1 2 a15 15 0 0 1 15 15" fill="none" stroke="#555" stroke-width="2.2"/>
      </svg>
    </div>
    <div><h3>Rss</h3><p>Lorem ipsum dolor sit amet...</p></div>
  </div>

  <h2 class="block-title" style="left:575px">In The Community</h2>
  <div class="gallery">
    <span role="img" aria-label="Community group photo" style="background:linear-gradient(#c9a27a,#6f8fb8)"></span>
    <span role="img" aria-label="Team members smiling" style="background:linear-gradient(#d8d8d8,#5e5a58)"></span>
    <span role="img" aria-label="Team at a local event" style="background:linear-gradient(#9fa9b2,#8a6d5f)"></span>
    <span role="img" aria-label="Friends in a circle" style="background:linear-gradient(#f2f2f2,#9c7d68)"></span>
    <span role="img" aria-label="Hands joined together" style="background:linear-gradient(#d69a7a,#8fb36b)"></span>
    <span role="img" aria-label="Group cheering outdoors" style="background:linear-gradient(#f4f4f4,#b27b5e)"></span>
  </div>

  <footer class="site-footer">
    <div class="agent-photo" role="img" aria-label="Portrait of Marisol Kettering, branch manager"></div>
    <div class="agent">
      <h3>Marisol Kettering<br>Branch Manager</h3>
      <ul>
        <li>Office: 555.204.3318</li>
        <li>Cell: 555.617.2094</li>
        <li>mkettering@brookvalefunding.example</li>
        <li>NMLS: 40219</li>
        <li>2470 Cedar Hollow Way, Ste. 110</li>
        <li>Maple Ridge, TX 75990</li>
      </ul>
      <a class="directions">Directions</a>
    </div>

    <div class="foot-col" style="left:409px">
      <h4>LINKS</h4>
      <ul>
        <li>Home</li><li>About</li><li>Builders</li><li>Mortgage Info</li><li>Approval</li><li>Blog</li><li>Contact Us</li>
      </ul>
    </div>

    <div class="foot-col" style="left:611px">
      <h4>ADDRESS</h4>
      <ul>
        <li>Our Address</li>
        <li>Corporate Office - 4820 Larkspur Avenue,</li>
        <li>Suite 300 Oakfield, Texas 75901</li>
        <li>&nbsp;</li>
        <li>Tel : 1-800-555-0176</li>
        <li>Email : Contact Brookvale Funding</li>
      </ul>
      <div class="lang">Language...
        <svg width="8" height="5" viewBox="0 0 8 5" aria-hidden="true"><path d="M1 1 L4 4 L7 1" fill="none" stroke="#c9c9c9" stroke-width="1.2"/></svg>
      </div>
    </div>
  </footer>

  <div class="footer-bar">
    <p class="copyright">Copyright © 2013 Brookvale Funding. All Rights Reserved</p>
    <div class="footer-badges">
      <span style="background:#4bb7e6"></span>
      <span style="background:#3b5a9a"></span>
      <span style="background:#e8732a"></span>
      <span style="background:transparent;border:2px solid #e6e6e6;border-radius:2px;margin-left:6px;width:26px;height:26px"></span>
    </div>
  </div>

</div>
</body>
</html>
```